Fresh, modern, fun business card for pediatric dental practice

Need a business card for fresh, modern, fun pediatric dental practice

Clean look that matches our website's font and colors

We prefer the look of curved corners on business cards

Target Market(s)

parents (mothers) of young children, professionals, mid-high class

Industry/Entity Type

Dental

Contact Information for Business Card

Maplebrook Pediatric Dentistry
482 Quarry Lane
Suite 517
Fernhollow, PA 10101
555.555.0193
www.maplebrookkidsdental.example

Mei-Ran Tsai, DMD
Corinne Walbeck, DMD
(we are working on our email address, but we would like that on the card as well)

Font styles to use
Sans Serif

Requirements
Must have
• All info; we would also like to make cards for individual staff members
• colors from our website and color palatte, attatched
• use same font and design as website for branding
Nice to have
• clean, simple card that has a pop of color
• we would like to see a few designs with our tag line "where smiles get brighter"
• we are not sure if we want to have it on there or not
• we would like to see a few designs incorporating the ribbon graphic on our website where the word WELCOME is

```html
<!DOCTYPE html>
<html lang="en">
<head>
<meta charset="utf-8">
<title>Maplebrook Pediatric Dentistry – Business Card</title>
<link href="https://fonts.googleapis.com/css2?family=Lato:wght@300;400;700&display=swap" rel="stylesheet">
<style>
  :root {
    --page: #141414;
    --card: #232323;
    --card-light: #2e2e2e;
    --sun: #f5b82e;
    --berry: #c8357f;
    --ink: #f2f2f2;
  }
  * { margin: 0; padding: 0; box-sizing: border-box; }
  html, body { width: 1200px; height: 897px; overflow: hidden; background: var(--page); }
  body { position: relative; font-family: "Lato", sans-serif; color: var(--ink); }

  .card {
    position: absolute;
    left: 304px;
    width: 594px;
    height: 338px;
    border-radius: 19px;
    background: linear-gradient(135deg, var(--card) 0%, var(--card) 55%, var(--card-light) 100%);
  }
  .card--front { top: 92px; }
  .card--back { top: 470px; }

  .brand { position: absolute; text-align: center; }
  .brand__mark { display: block; margin: 0 auto; border-radius: 50%; background: var(--sun); }
  .brand__name { display: block; line-height: 1; color: var(--sun); font-weight: 700; }
  .brand__tag { display: block; line-height: 1; color: var(--berry); font-weight: 400; }

  .card--front .brand { left: 60px; width: 220px; top: 104px; }
  .card--front .brand__mark { width: 38px; height: 38px; margin-bottom: 12px; }
  .card--front .brand__name { font-size: 33px; letter-spacing: 1px; }
  .card--front .brand__tag { font-size: 17px; letter-spacing: 1.6px; margin-top: 4px; }

  .divider { position: absolute; left: 296px; top: 100px; width: 2px; height: 116px; background: var(--berry); }

  .person { position: absolute; left: 323px; top: 96px; }
  .person__name { font-size: 21px; font-weight: 700; color: var(--sun); letter-spacing: 0.8px; text-transform: uppercase; }
  .person__title { font-size: 15px; margin-top: 4px; letter-spacing: 0.5px; }

  .contact { position: absolute; left: 331px; top: 165px; list-style: none; font-size: 13px; }
  .contact li { display: flex; align-items: center; height: 19px; white-space: nowrap; }
  .contact svg { width: 11px; height: 11px; margin-right: 9px; flex: none; fill: none; stroke: var(--sun); stroke-width: 1.6; }
  .contact svg.solid { fill: var(--sun); stroke: none; }

  .practice { position: absolute; left: 0; right: 0; top: 276px; text-align: center; }
  .practice__name { font-size: 14px; font-weight: 700; color: var(--sun); letter-spacing: 0.5px; text-transform: uppercase; }
  .practice__address { font-size: 15px; margin-top: 4px; letter-spacing: 0.4px; }

  .card--back .brand { left: 0; right: 0; top: 90px; }
  .card--back .brand__mark { width: 56px; height: 56px; margin-bottom: 18px; }
  .card--back .brand__name { font-size: 54px; letter-spacing: 2px; }
  .card--back .brand__tag { font-size: 26px; letter-spacing: 2.6px; margin-top: 4px; }

  .web { position: absolute; left: 0; right: 0; top: 292px; text-align: center; font-size: 15px; letter-spacing: 1.8px; }
  .web__domain { color: var(--sun); }
</style>
</head>
<body>

<section class="card card--front">
  <div class="brand">
    <span class="brand__mark"></span>
    <span class="brand__name">maplebrook</span>
    <span class="brand__tag">pediatric dentistry</span>
  </div>

  <div class="divider"></div>

  <div class="person">
    <p class="person__name">Corinne Walbeck</p>
    <p class="person__title">DMD</p>
  </div>

  <ul class="contact">
    <li>
      <svg class="solid" viewBox="0 0 12 12" aria-hidden="true"><path d="M2.2 0.8 L4 0.5 L5 3 L3.8 4 C4.4 5.6 6.4 7.6 8 8.2 L9 7 L11.5 8 L11.2 9.8 C10.8 11 9.5 11.5 8 11 C4.6 9.8 2.2 7.4 1 4 C0.5 2.5 1 1.2 2.2 0.8 Z"/></svg>
      555.555.0193
    </li>
    <li>
      <svg viewBox="0 0 12 12" aria-hidden="true"><rect x="1" y="2.5" width="10" height="7"/><path d="M1 2.5 L6 6.5 L11 2.5"/></svg>
      info@maplebrookkidsdental.example
    </li>
    <li>
      <svg viewBox="0 0 12 12" aria-hidden="true"><circle cx="6" cy="6" r="5"/><ellipse cx="6" cy="6" rx="2.2" ry="5"/><path d="M1 6 H11 M2 3.5 H10 M2 8.5 H10"/></svg>
      www.maplebrookkidsdental.example
    </li>
  </ul>

  <div class="practice">
    <p class="practice__name">Maplebrook Pediatric Dentistry</p>
    <p class="practice__address">482 Quarry Lane Suite 517 Fernhollow, PA 10101</p>
  </div>
</section>

<section class="card card--back">
  <div class="brand">
    <span class="brand__mark"></span>
    <span class="brand__name">maplebrook</span>
    <span class="brand__tag">pediatric dentistry</span>
  </div>
  <p class="web">www.<span class="web__domain">maplebrookkidsdental</span>.example</p>
</section>

</body>
</html>
```